Webshop facelift - modern, sales oriented, mobile first

We need facelifted webshop, which is running for few years.
www.pelvaro.si
Some of the basic requirements:

1.) Logo must basicly stay the same, it could only be a little "modernised".
2.) Main goal is to generate more sales, so webpage must be much more sales oriented.
3.) Focus is on category page and product page. Those two page types must be realy designed very well
4.) Mobile first, there are 80% customers over mobile devices
5.) Mobile menu must be also much better
6.) Category description will go under listed products
7.) On product page, there must be much bigger product images, and also mobile friendly image slider
8.) Big add to cart buttons
9.) Badges about safe shopping, possible returning goods, 100% warranty
10.) exposed product videos, images between text
11.) cleary exposed product benefits
11.) Products, which have sizes to choose, must have more user friendly choose option
12.) category page on desktop can have only products in all width, not side menu on the left
13.) Exposed CTA's on product page

You can create this category page: https://pelvaro.si/posteljnina
You can create this product page: https://pelvaro.si/oblikovalne-hlacke-kvarcit-shorts

In short: mobile first, very sales oriented, look like 2018, big images, great shopping experience.

Target Market(s)

6 European coutries

Industry/Entity Type

E-Commerce

Number of Pages Required

3 page

Font styles to use
Sans Serif

Colors

Designer to choose colors to be used in the design.

Requirements
Must have
• Mobile first design
• Big images
• Very sales oriented
• CTA's through product description
Nice to have
• Product badges, like for example "100% cotton", "On stock", "Sale", "New"
Should not have
• Should not be copied from somewhere.

```html
<!DOCTYPE html>
<html lang="sl">
<head>
<meta charset="utf-8">
<title>Lumivo – Moški</title>
<link rel="stylesheet" href="https://fonts.googleapis.com/css2?family=Poppins:wght@300;400;500;600&display=swap">
<style>
:root{
  --ink:#2b2b2b;
  --muted:#8a8a8a;
  --line:#e4e4e4;
  --accent:#4f73b3;
  --brand:#e0892a;
  --star:#f2b01e;
  --paper:#ffffff;
  --hero-a:#d9d9d9;
  --hero-b:#a9a9a9;
  --img-a:#e9e3dc;
  --img-b:#cfc6bc;
}
*{box-sizing:border-box;margin:0;padding:0}
html,body{width:1200px;height:800px;overflow:hidden;background:var(--paper)}
body{font-family:"Poppins",sans-serif;color:var(--ink);font-size:12px}
.page{position:relative;width:1200px;height:800px;overflow:hidden}

.hero{position:relative;height:220px}
.hero-photo{position:absolute;inset:0;background:linear-gradient(135deg,var(--hero-a) 0%,#c4c4c4 45%,var(--hero-b) 100%)}
.topbar{position:relative;display:flex;align-items:center;justify-content:space-between;padding:18px 60px}
.brand{display:flex;align-items:center;gap:8px;font-weight:600;font-size:18px;color:var(--brand)}
.brand-dot{width:18px;height:18px;border-radius:50%;background:var(--brand)}
.main-nav{display:flex;gap:18px;font-size:10px;font-weight:500;letter-spacing:.04em;color:var(--ink)}
.nav-tools{display:flex;gap:12px;align-items:center}
.breadcrumb{position:absolute;left:0;right:0;top:150px;text-align:center;font-size:11px;font-weight:500;color:#fff;letter-spacing:.05em}
.breadcrumb span{margin:0 6px}

.content{display:flex;gap:30px;padding:36px 150px 0 150px}
.sidebar{width:190px;flex:none}
.panel-head{background:var(--accent);color:#fff;font-size:11px;font-weight:500;padding:8px 12px;letter-spacing:.04em}
.cat-list{list-style:none;border:1px solid var(--line);border-top:none;margin-bottom:22px}
.cat-list li{display:flex;justify-content:space-between;padding:6px 12px;border-bottom:1px solid var(--line);font-size:10px;text-transform:uppercase}
.cat-list li.sub{padding-left:22px;text-transform:none;color:var(--muted)}
.cat-list li:last-child{border-bottom:none}
.filter{border:1px solid var(--line);border-top:none;padding:10px 12px;font-size:10px}
.filter h4{font-size:10px;font-weight:600;text-transform:uppercase;margin:6px 0 5px}
.filter .range{color:var(--muted)}
.swatches{display:grid;grid-template-columns:1fr 1fr;gap:4px}
.swatch{display:flex;align-items:center;gap:6px;color:var(--muted)}
.swatch i{width:9px;height:9px;display:inline-block}
.sizes{display:grid;grid-template-columns:1fr 1fr;gap:4px;color:var(--muted)}
.sizes label::before{content:"";display:inline-block;width:8px;height:8px;border:1px solid #bbb;margin-right:6px;vertical-align:-1px}

.listing{flex:1}
.toolbar{display:flex;justify-content:space-between;align-items:center;padding-bottom:12px;border-bottom:1px solid var(--line);font-size:10px;color:var(--muted)}
.view-toggle{display:flex;gap:6px}
.view-toggle i{width:12px;height:12px;background:var(--accent);display:block}
.view-toggle i+i{background:#555}
.sort{border:1px solid var(--line);padding:5px 10px}
.product{display:flex;gap:26px;padding:18px 0;border-bottom:1px solid var(--line)}
.product-photo{width:160px;height:150px;flex:none;background:linear-gradient(160deg,var(--img-a),var(--img-b))}
.product-body{flex:1}
.product-brand{font-size:11px;font-weight:600;margin-bottom:6px}
.product-title{font-size:13px;font-weight:500;margin-bottom:4px}
.stars{color:var(--star);font-size:11px;letter-spacing:2px}
.price{margin:4px 0;font-size:14px;color:var(--accent);font-weight:600}
.price s{color:var(--muted);font-weight:400;font-size:11px;margin-left:8px}
.desc{font-size:10px;color:var(--muted);line-height:1.6;max-width:420px;margin-bottom:10px}
.actions{display:flex;gap:6px;align-items:center}
.btn-cart{background:var(--accent);color:#fff;border:none;font:500 10px "Poppins",sans-serif;padding:8px 14px}
.icon-btn{width:24px;height:24px;border:1px solid var(--line);display:flex;align-items:center;justify-content:center;font-size:11px}
</style>
</head>
<body>
<div class="page">
  <header class="hero">
    <div class="hero-photo" role="img" aria-label="Črno-bela fotografija tipkovnice z majhnim nakupovalnim vozičkom"></div>
    <div class="topbar">
      <div class="brand"><span class="brand-dot"></span>Lumivo</div>
      <nav class="main-nav">
        <span>DOM IN VRT</span><span>OBLAČILA</span><span>POSTELJNINA</span><span>OTROCI</span><span>LEPOTA</span><span>DEKOR</span><span>DARILA</span><span>PIKNIK &amp; PARTY</span>
      </nav>
      <div class="nav-tools">
        <svg width="12" height="12" viewBox="0 0 12 12"><circle cx="5" cy="5" r="3.5" fill="none" stroke="#2b2b2b" stroke-width="1.4"/><line x1="7.6" y1="7.6" x2="11" y2="11" stroke="#2b2b2b" stroke-width="1.4"/></svg>
        <svg width="14" height="12" viewBox="0 0 14 12"><path d="M1 1h2l2 7h7l1.5-5H4" fill="none" stroke="#2b2b2b" stroke-width="1.3"/><circle cx="6" cy="10.5" r="1" fill="#2b2b2b"/><circle cx="11" cy="10.5" r="1" fill="#2b2b2b"/></svg>
        <svg width="12" height="12" viewBox="0 0 12 12"><circle cx="6" cy="6" r="4.5" fill="none" stroke="#2b2b2b" stroke-width="1.4"/><circle cx="6" cy="6" r="1.5" fill="#2b2b2b"/></svg>
      </div>
    </div>
    <div class="breadcrumb">HOME<span>›</span>FASHION<span>›</span>MEN</div>
  </header>

  <main class="content">
    <aside class="sidebar">
      <div class="panel-head">≡ CATEGORY</div>
      <ul class="cat-list">
        <li>Women</li>
        <li class="sub">Clothing <span>›</span></li>
        <li class="sub">Shoes <span>›</span></li>
        <li class="sub">Hat <span>›</span></li>
        <li class="sub">Bag <span>›</span></li>
        <li>Men <span>›</span></li>
        <li>Shop <span>›</span></li>
        <li>Accessories <span>›</span></li>
      </ul>
      <div class="panel-head">≡ FILTER PRODUCTS BY</div>
      <div class="filter">
        <h4>Price</h4>
        <p class="range">Range: $00.00 – $100.00</p>
        <h4>Colors</h4>
        <div class="swatches">
          <span class="swatch"><i style="background:#111"></i>Black (5)</span>
          <span class="swatch"><i style="background:#2f5fc4"></i>Blue (4)</span>
          <span class="swatch"><i style="background:#8cc63f"></i>Green (3)</span>
          <span class="swatch"><i style="background:#f07ab0"></i>Pink (2)</span>
          <span class="swatch"><i style="background:#d92b2b"></i>Red (6)</span>
          <span class="swatch"><i style="background:#f5d311"></i>Yellow (1)</span>
        </div>
        <h4>Size</h4>
        <div class="sizes">
          <label>S (4)</label><label>M (6)</label><label>L (3)</label><label>One size (2)</label>
        </div>
      </div>
    </aside>

    <section class="listing">
      <div class="toolbar">
        <div class="view-toggle"><i></i><i></i></div>
        <div>Showing 1–8 of 30 results &nbsp; <span class="sort">SORT BY POPULARITY ▾</span></div>
      </div>

      <article class="product">
        <div class="product-photo" role="img" aria-label="Električni odstranjevalec kalusa ob stopalu"></div>
        <div class="product-body">
          <p class="product-brand">NovaDom</p>
          <h3 class="product-title">Električni odstranjevalec kalusa NovaDom</h3>
          <div class="stars">★★★★★</div>
          <p class="price">$126.00<s>$150.00</s></p>
          <p class="desc">Lorem ipsum dolor sit amet, consectetur adipiscing elit, sed diam nonummy nibh euismod tincidunt ut laoreet dolore magna aliquam erat volutpat.</p>
          <div class="actions"><button class="btn-cart">Add to cart</button><span class="icon-btn">♡</span><span class="icon-btn">⇄</span><span class="icon-btn">⌕</span></div>
        </div>
      </article>

      <article class="product">
        <div class="product-photo" role="img" aria-label="Predpasnik za britje brade v kopalnici"></div>
        <div class="product-body">
          <p class="product-brand">NovaDom</p>
          <h3 class="product-title">Predpasnik za lovljenje obrezane brade</h3>
          <div class="stars">★★★★★</div>
          <p class="price">$126.00<s>$150.00</s></p>
          <p class="desc">Lorem ipsum dolor sit amet, consectetur adipiscing elit, sed diam nonummy nibh euismod tincidunt ut laoreet dolore magna aliquam erat volutpat.</p>
          <div class="actions"><button class="btn-cart">Add to cart</button><span class="icon-btn">♡</span><span class="icon-btn">⇄</span><span class="icon-btn">⌕</span></div>
        </div>
      </article>

      <article class="product">
        <div class="product-photo" role="img" aria-label="Aparat za beljenje zob"></div>
        <div class="product-body">
          <p class="product-brand">NovaDom</p>
          <h3 class="product-title">Aparat za beljenje in poliranje zob NovaDom</h3>
          <div class="stars">★★★★★</div>
          <p class="price">$126.00<s>$150.00</s></p>
        </div>
      </article>
    </section>
  </main>
</div>
</body>
</html>
```